Coastal Gin Label Design

We are needing a nautical/coastal themed label for our upcoming gin release.

We have saltbush, cucumber, juniper, and quandong being used in this gin.

Name of the Gin; Harbour Moons

The logo attached is the company logo, but doesn't have to be used on the front of the label, ie it can just be the name Fernwhistle somewhere on the front.
Bottle specs attached as well so you can accurately represent the bottle- this bottle is also clear.

Target Market(s)

Women 25- 45

Font styles to use
Serif
Decorative

Colors
d5edf4
86cae7
33a6d7
86cfc6
cfeae6
ffffff
f6faec
ecf7fb
fefeff

Requirements
Must have
• Ocean/Coastal vibe to the label
Nice to have
• Blues,Whites clean and crisp
Should not have
• No generic word art look to it.
A dark mood

```html
<!DOCTYPE html>
<html lang="en">
<head>
<meta charset="utf-8">
<title>Harbour Moons Gin Label</title>
<link href="https://fonts.googleapis.com/css2?family=Abril+Fatface&family=Cormorant+Garamond:wght@500&family=Josefin+Sans:wght@600&family=Oswald:wght@400&display=swap" rel="stylesheet">
<style>
  :root {
    --page: #ffffff;
    --sea-deep: #0e8a80;
    --sea: #1fa99c;
    --sea-light: #5cc4b9;
    --sand: #e6dcc2;
    --foam: #ffffff;
    --title-dark: #0f6f68;
    --title-mid: #1a968b;
    --title-light: #55bdb5;
    --ink-light: #ffffff;
  }
  html, body {
    margin: 0;
    width: 1200px;
    height: 1193px;
    overflow: hidden;
    background: var(--page);
  }
  .label {
    position: absolute;
    left: 331px;
    top: 273px;
    width: 530px;
    height: 670px;
    overflow: hidden;
    box-shadow: 0 2px 10px rgba(0,0,0,0.12);
  }
  .label__scene {
    position: absolute;
    inset: 0;
    background: linear-gradient(125deg,
      var(--sea) 0%, var(--sea-light) 14%, var(--sand) 26%,
      var(--foam) 36%, var(--foam) 52%, var(--sand) 57%,
      var(--sea-light) 60%, var(--sea) 66%, var(--sea-deep) 100%);
  }
  .label__brand {
    position: absolute;
    left: 34px;
    top: 22px;
    margin: 0;
    font-family: "Cormorant Garamond", serif;
    font-weight: 500;
    font-size: 29px;
    letter-spacing: 0.5px;
    color: var(--ink-light);
  }
  .label__title {
    position: absolute;
    left: -15px;
    top: 105px;
    width: 560px;
    margin: 0;
    transform: rotate(-16deg);
    transform-origin: center;
    font-family: "Abril Fatface", serif;
    font-weight: 400;
    line-height: 0.92;
    text-align: center;
    letter-spacing: 1px;
    background: linear-gradient(200deg, var(--title-light) 0%, var(--title-mid) 45%, var(--title-dark) 100%);
    -webkit-background-clip: text;
    background-clip: text;
    color: transparent;
  }
  .label__title-line { display: block; }
  .label__title-line--top { font-size: 88px; }
  .label__title-line--bottom { font-size: 112px; }
  .label__type {
    position: absolute;
    left: 0;
    width: 100%;
    top: 470px;
    margin: 0;
    text-align: center;
    font-family: "Josefin Sans", sans-serif;
    font-weight: 600;
    font-size: 64px;
    line-height: 1;
    letter-spacing: 10px;
    padding-left: 10px;
    box-sizing: border-box;
    color: var(--ink-light);
    text-shadow: 0 2px 5px rgba(0,60,55,0.45);
  }
  .label__rule {
    position: absolute;
    left: 139px;
    top: 578px;
    width: 250px;
    height: 2px;
    background: var(--ink-light);
  }
  .label__specs {
    position: absolute;
    left: 0;
    width: 100%;
    top: 587px;
    margin: 0;
    text-align: center;
    font-family: "Oswald", sans-serif;
    font-size: 21px;
    color: var(--ink-light);
    word-spacing: 2px;
    text-shadow: 0 1px 3px rgba(0,60,55,0.4);
  }
  .label__specs span + span { margin-left: 24px; }
</style>
</head>
<body>
  <div class="label">
    <div class="label__scene" role="img" aria-label="Aerial photograph of turquoise sea waves breaking over a sandy shore"></div>
    <p class="label__brand">FERNWHISTLE</p>
    <h1 class="label__title">
      <span class="label__title-line label__title-line--top">HARBOUR</span>
      <span class="label__title-line label__title-line--bottom">MOONS</span>
    </h1>
    <p class="label__type">GIN</p>
    <div class="label__rule"></div>
    <p class="label__specs"><span>42% ALC/VOL</span><span>750ML</span></p>
  </div>
</body>
</html>
```